Business Cards + Flyer + Letterhead for Care Recruitment Agency

We are a recruitment agency for the health & care sector. We need designs made for business cards, A5 double-sided flyer, and a letterhead template.

Our branding message is professionalism, care, compassion, expertise. We are experts in recruitment for the care & health industry.

Our logo source files and colours are here - https://www.filevault-example.net/sh/q8rn27lpzw4xkc/BBRtLm3QPW92dKfYhNvZceLmo?dl=0

For the business card, I have attached an example we like. We want a vertical business card design, something very similar to the example given. The design should match our logo in terms of brand colors. On one side should be our logo, our website (www.holbrookelune.co.uk) and Care Recruitment Specialists written somewhere visible that fits, between our logo and the website at the bottom. On the other side should be our details.

Details on the front:

Logo with slogan
Care Recruitment Specialists
www.holbrookelune.co.uk

Details on the back:

Dominic Argyros
Managing Director

Radley Court, 40-48 Pellow St, Birmingham, B7 9QX
07612 495137
dominic@holbrookelune.co.uk
www.holbrookelune.co.uk

Nadia Holbrooke
Business Development Director

07731 284956
nadia@holbrookelune.co.uk
www.holbrookelune.co.uk

For the A5 flyer, I have attached some pictures we've used for the website, which could be used for the flyer as well. To get a better idea of our branding, please visit our website - https://holbrookelune.co.uk/

The text for the flyer is also attached.

Finally, the letterhead template should be a docx template with our logo and our identifiable branding (the same shapes and matching colours you will come up with for the business cards and flyer).

```html
<!DOCTYPE html>
<html lang="en">
<head>
<meta charset="utf-8">
<title>Holbrooke Lune – Business Card</title>
<link rel="stylesheet" href="https://fonts.googleapis.com/css2?family=Montserrat:wght@500;700&family=Roboto:wght@400;500&display=swap">
<style>
  :root {
    --backdrop: #d9d9d7;
    --card-white: #ffffff;
    --navy: #13306e;
    --brand-blue: #1a7ff0;
    --sky-blue: #17c3f5;
    --text-grey: #555a60;
    --blue-top: #0a6dff;
    --blue-bottom: #05bdf5;
    --emboss-blue: #1767d8;
    --pale-blue: #cdeeff;
  }
  * { margin: 0; padding: 0; box-sizing: border-box; }
  html, body {
    width: 1200px; height: 801px; overflow: hidden;
    background: var(--backdrop);
  }
  .stage {
    width: 1200px; height: 801px;
    display: flex; align-items: center; justify-content: center; gap: 60px;
  }

  /* Details side – portrait */
  .card-details {
    width: 360px; height: 560px;
    background: var(--card-white);
    box-shadow: 0 6px 18px rgba(0,0,0,.18);
    padding: 80px 34px 40px;
    display: flex; flex-direction: column;
  }
  .brand-lockup {
    display: flex; align-items: center; justify-content: center; gap: 10px;
  }
  .brand-mark {
    width: 16px; height: 16px; border-radius: 50%;
    background: var(--brand-blue); flex: none;
  }
  .brand-name {
    font-family: 'Roboto', sans-serif; font-weight: 500;
    font-size: 26px; color: var(--navy); white-space: nowrap;
  }
  .contact-block { margin-top: auto; }
  .person-name {
    font-family: 'Montserrat', sans-serif; font-weight: 700;
    font-size: 21px; color: var(--sky-blue); text-transform: uppercase;
    letter-spacing: .5px; white-space: nowrap;
  }
  .person-role {
    font-family: 'Roboto', sans-serif; font-weight: 500;
    font-size: 15px; color: var(--text-grey); margin: 2px 0 14px;
  }
  .address, .contact-line {
    font-family: 'Roboto', sans-serif; font-size: 15px;
    color: var(--text-grey); line-height: 1.35;
  }
  .address { margin-bottom: 2px; }
  .contact-line { display: flex; align-items: center; gap: 7px; white-space: nowrap; }
  .contact-line svg { width: 14px; height: 14px; flex: none; }

  /* Brand side – landscape */
  .card-brand {
    width: 560px; height: 360px;
    background: linear-gradient(160deg, var(--blue-top) 0%, var(--blue-bottom) 100%);
    box-shadow: 0 6px 18px rgba(0,0,0,.18);
    position: relative;
    display: flex; align-items: center; justify-content: center;
  }
  .card-brand .brand-lockup { gap: 16px; margin-top: -40px; }
  .card-brand .brand-mark { width: 40px; height: 40px; background: var(--emboss-blue); }
  .card-brand .brand-name { color: var(--emboss-blue); font-size: 40px; }
  .specialists, .brand-web {
    position: absolute; width: 100%; text-align: center; color: var(--pale-blue);
  }
  .specialists {
    bottom: 78px;
    font-family: 'Montserrat', sans-serif; font-weight: 500;
    font-size: 13px; letter-spacing: 3px;
  }
  .brand-web {
    bottom: 36px;
    font-family: 'Roboto', sans-serif; font-size: 14px; letter-spacing: .5px;
  }
</style>
</head>
<body>
<main class="stage">

  <section class="card-details">
    <div class="brand-lockup">
      <span class="brand-mark"></span>
      <span class="brand-name">Holbrooke Lune</span>
    </div>

    <div class="contact-block">
      <h1 class="person-name">Dominic Argyros</h1>
      <p class="person-role">Managing Director</p>
      <p class="address">Radley Court,<br>40-48 Pellow St,<br>Birmingham, B7 9QX</p>
      <p class="contact-line">
        <svg viewBox="0 0 16 16"><path fill="#1a7ff0" d="M3 1h3l1.5 4-2 1.3a9 9 0 0 0 4.2 4.2l1.3-2 4 1.5v3a1.5 1.5 0 0 1-1.5 1.5A13 13 0 0 1 1.5 2.5 1.5 1.5 0 0 1 3 1z"/></svg>
        07612 495137
      </p>
      <p class="contact-line">
        <svg viewBox="0 0 16 16"><rect x="1" y="3" width="14" height="10" fill="#1a7ff0"/><path d="M1 3l7 6 7-6" fill="none" stroke="#fff" stroke-width="1.2"/></svg>
        dominic@holbrookelune.co.uk
      </p>
      <p class="contact-line">
        <svg viewBox="0 0 16 16"><circle cx="8" cy="8" r="7" fill="#1a7ff0"/><path d="M1 8h14M8 1c-3 3.5-3 10.5 0 14M8 1c3 3.5 3 10.5 0 14" fill="none" stroke="#fff" stroke-width="1"/></svg>
        www.holbrookelune.co.uk
      </p>
    </div>
  </section>

  <section class="card-brand">
    <div class="brand-lockup">
      <span class="brand-mark"></span>
      <span class="brand-name">Holbrooke Lune</span>
    </div>
    <p class="specialists">CARE RECRUITMENT SPECIALISTS</p>
    <p class="brand-web">www.holbrookelune.co.uk</p>
  </section>

</main>
</body>
</html>
```